TV Antenna Installation business needs a unique flyer

We need a simple but effective flyer design for our TV Aerial installation company based in Newcastle, NSW, Australia called Bright Harbour TV & Aerial Svcs.
We are trying to target areas where there has been a new transmitter installed and most houses just require their aerial redirecting and tv's retuning.

Industry/Entity Type

Business

Requirements
Must have
• We would like the idea of a headline phrase such as " Poor TV reception……..now a thing from the past" or something similar & catchy.
Also "Did you know a new transmitter has been recently installed in your area, we can therefore now GUARANTEE 100% PERFECT PICTURE
Charges from only $95.
- Free 5 year warranty
- Free signal testing
- Free Onsite Quote
Phone 0463 527 209
Nice to have
• Other services include:

- New Installs
- Extra Points & repairs
- TV wall mounting/Home Cinema
- Pull down tall masts

Modern tv picture, see example uploaded

```html
<!DOCTYPE html>
<html lang="en">
<head>
<meta charset="utf-8">
<title>Bright Harbour TV &amp; Aerial Svcs – Flyer</title>
<link rel="stylesheet" href="https://fonts.googleapis.com/css2?family=Comic+Neue:wght@700&family=Ubuntu:wght@700&family=Archivo+Black&family=Arimo:wght@700&display=swap">
<style>
  :root {
    --navy: #2e3192;
    --lime: #bfd73c;
    --crimson: #c4163a;
    --red: #e31e26;
    --deep-red: #8e0f1c;
    --yellow: #ffe600;
    --ink: #222222;
    --paper: #ffffff;
    --halo: #e4e4ea;
  }
  * { margin: 0; padding: 0; box-sizing: border-box; }
  html, body { width: 871px; height: 1200px; overflow: hidden; background: var(--paper); }
  .flyer { position: relative; width: 871px; height: 1200px; background: var(--paper); overflow: hidden; }
  .backdrop { position: absolute; inset: 0; }

  .tv-art {
    position: absolute; left: 65px; top: 42px; width: 290px; height: 355px;
    border-radius: 40px;
    background: radial-gradient(ellipse at 50% 45%, #3b3f9a 0%, #a4522c 55%, #d9d9d9 100%);
  }

  .headline {
    position: absolute; left: 466px; top: 108px;
    font-family: "Comic Neue", "Comic Sans MS", cursive; font-weight: 700;
    color: var(--navy);
    text-shadow: 3px 0 0 var(--halo), -3px 0 0 var(--halo), 0 3px 0 var(--halo), 0 -3px 0 var(--halo),
                 2px 2px 0 var(--halo), -2px -2px 0 var(--halo), 2px -2px 0 var(--halo), -2px 2px 0 var(--halo);
  }
  .headline__big { display: block; font-size: 76px; line-height: 1; letter-spacing: 1px; }
  .headline__small { display: block; font-size: 40px; line-height: 1.2; }
  .headline__reception { margin-left: 40px; margin-top: 6px; }
  .headline__past { margin-top: 22px; }

  .brand {
    position: absolute; left: 0; width: 871px; top: 440px; text-align: center;
    font-family: "Ubuntu", sans-serif; font-weight: 700; font-size: 54px; color: var(--crimson);
  }

  .pitch {
    position: absolute; left: 0; width: 871px; top: 576px; text-align: center;
    font-family: "Arimo", Arial, sans-serif; font-weight: 700; font-size: 27px; line-height: 48px; color: var(--ink);
  }
  .pitch__guarantee { display: block; font-size: 35px; line-height: 44px; color: var(--navy); }

  .price {
    position: absolute; left: 45px; top: 730px; width: 780px; height: 140px;
    border-radius: 50%; border: 5px solid var(--red);
    background: radial-gradient(ellipse at 50% 40%, var(--red) 0%, #b3121f 55%, var(--deep-red) 100%);
    display: flex; align-items: center; justify-content: center; gap: 16px;
    font-family: "Archivo Black", "Arial Black", sans-serif; color: var(--paper);
  }
  .price__label { font-size: 38px; letter-spacing: 1px; }
  .price__amount { font-size: 62px; color: var(--yellow); }

  .perks {
    position: absolute; left: 42px; top: 894px; list-style: none;
    font-family: "Archivo Black", "Arial Black", sans-serif; font-size: 30px; color: var(--navy);
  }
  .perks li { height: 60px; line-height: 50px; }
  .perks li:last-child { margin-top: 4px; }

  .divider { position: absolute; left: 434px; top: 906px; width: 3px; height: 176px; background: var(--paper); border-radius: 2px; }

  .services { position: absolute; left: 470px; top: 882px; font-family: "Arimo", Arial, sans-serif; font-weight: 700; }
  .services__title { font-size: 33px; color: var(--crimson); margin-bottom: 10px; }
  .services__list { list-style: none; }
  .services__item { display: flex; align-items: center; gap: 16px; font-size: 19px; color: var(--ink); height: 36px; }
  .services__tick { width: 22px; height: 22px; flex: none; }

  .contact {
    position: absolute; left: 120px; top: 1104px; width: 630px; height: 192px;
    border-radius: 50%; background: var(--navy);
  }
  .contact__line {
    position: absolute; left: 0; width: 871px; top: 1128px; text-align: center;
    display: flex; justify-content: center; align-items: center; gap: 8px;
    font-family: "Arimo", Arial, sans-serif; font-weight: 700; font-size: 46px; color: var(--paper);
  }
  .contact__icon { width: 40px; height: 40px; }
</style>
</head>
<body>
<main class="flyer">
  <svg class="backdrop" width="871" height="1200" viewBox="0 0 871 1200" aria-hidden="true">
    <rect x="0" y="446" width="871" height="754" fill="var(--lime)"/>
    <path d="M0 0 H871 V446 Q435 650 0 446 Z" fill="var(--paper)"/>
    <path d="M30 456 Q435 600 840 456 Q435 570 30 456 Z" fill="var(--navy)"/>
  </svg>

  <div class="tv-art" role="img" aria-label="Illustration of a retro television set with a no-signal symbol on its screen"></div>

  <h1 class="headline">
    <span class="headline__big">Poor TV</span>
    <span class="headline__small headline__reception">reception……..</span>
    <span class="headline__small headline__past">now a thing</span>
    <span class="headline__small">from the past</span>
  </h1>

  <div class="brand">Bright Harbour</div>

  <p class="pitch">
    Did you know a new transmitter has been<br>
    recently installed in your area, we can therefore now
    <span class="pitch__guarantee">GUARANTEE 100% PERFECT PICTURE</span>
  </p>

  <div class="price">
    <span class="price__label">Charges from only</span>
    <span class="price__amount">$95</span>
  </div>

  <ul class="perks">
    <li>Free 5 year warranty</li>
    <li>Free signal testing</li>
    <li>Free Onsite Quote</li>
  </ul>

  <div class="divider"></div>

  <section class="services">
    <h2 class="services__title">Our services</h2>
    <ul class="services__list">
      <li class="services__item"><svg class="services__tick" viewBox="0 0 22 22" aria-hidden="true"><rect x="2" y="5" width="14" height="14" fill="none" stroke="var(--crimson)" stroke-width="2"/><path d="M5 11 L9 15 L20 2" fill="none" stroke="var(--crimson)" stroke-width="3"/></svg>New Installs</li>
      <li class="services__item"><svg class="services__tick" viewBox="0 0 22 22" aria-hidden="true"><rect x="2" y="5" width="14" height="14" fill="none" stroke="var(--crimson)" stroke-width="2"/><path d="M5 11 L9 15 L20 2" fill="none" stroke="var(--crimson)" stroke-width="3"/></svg>Extra Points &amp; repairs</li>
      <li class="services__item"><svg class="services__tick" viewBox="0 0 22 22" aria-hidden="true"><rect x="2" y="5" width="14" height="14" fill="none" stroke="var(--crimson)" stroke-width="2"/><path d="M5 11 L9 15 L20 2" fill="none" stroke="var(--crimson)" stroke-width="3"/></svg>TV wall mounting/Home Cinema</li>
      <li class="services__item"><svg class="services__tick" viewBox="0 0 22 22" aria-hidden="true"><rect x="2" y="5" width="14" height="14" fill="none" stroke="var(--crimson)" stroke-width="2"/><path d="M5 11 L9 15 L20 2" fill="none" stroke="var(--crimson)" stroke-width="3"/></svg>Pull down tall masts</li>
    </ul>
  </section>

  <div class="contact"></div>
  <p class="contact__line">
    <svg class="contact__icon" viewBox="0 0 40 40" aria-hidden="true"><circle cx="20" cy="20" r="17" fill="none" stroke="#5aa9e6" stroke-width="2"/><path d="M14 10 L18 14 L15 17 Q18 23 23 25 L26 22 L30 26 L27 30 Q16 30 10 14 Z" fill="#5aa9e6"/></svg>
    0463 527 209
  </p>
</main>
</body>
</html>
```